Car wash line needed for the pylon inscription

We need a design template / print template for our advertising pylon so that the Korvane plates can be printed. The area to be printed is approx. 1.5m wide and approx. 2.70m high. We operate a car wash about 30m long. The washing rollers are equipped with scratch-free Velmo Tex foam material. Before the vehicle is put into the car wash it gets a manual high pressure pre-wash. There are four different washing programs: basic laundry € 7.50 (wheel cleaning, intensive washing, gloss drying comfort care € 10.50 (like base + active foam) special care € 13.00 (like comfort + glossy sealing with lotus wax) premium care € 15.50 (like special care + Underbody wash) The pylon is right on the driveway on a busy road, we want to achieve maximum attention with the pylons. It should not be too much content because the vehicles drive past it, due to an immediate gyro, the speed is however at about 40Km / h. Opening hours Mon-Fri. 08: 00-19: 00 Sat 07: 00-19: 00 The Korvane plates are red. The enclosed files show our pylon with a little appealing design proposal our advertising agency and the real local places. For the opinion you can see on the following link a youtube video with a comparable car wash like ours, the washing process is well illustrated there. https://www.clipvault-demo.net/watch?v=Qk7rTzP2mLw Furthermore, we have a bonus card system who has washed our car 10 times gets the 11 laundry for free. From foam additives we use active foam from the comfort care and from the special care gets the vehicle lotus wax, which has the effect that the paint is sealed and keeps the shine longer. We need a design template / print template for our advertising pylon so that the Korvane plates can be printed. The area to be printed is approx. 1.5m wide and approx. 2.70m high. We operate a car wash about 30m long. The washing rollers are equipped with scratch-free Velmo Tex foam material. Before the vehicle is put into the car wash it gets a manual high pressure pre-wash. There are four different washing programs: basic laundry € 7.50 (wheel cleaning, intensive washing, gloss drying comfort care € 10.50 (like base + active foam) special care € 13.00 (like comfort + glossy sealing with lotus wax) premium care € 15.50 (like special care + Underbody wash) The pylon is right on the driveway on a busy road, we want to achieve maximum attention with the pylons. It should not be too much content because the vehicles drive past it, due to an immediate gyro, the speed is however at about 40Km / h. Opening hours Mon-Fri. 08: 00-19: 00 Sat 07: 00-19: 00 The Korvane plates are red. The enclosed files show our pylon with a little appealing design proposal our advertising agency and the real local places. For the opinion you can see on the following link a youtube video with a comparable car wash like ours, the washing process is well illustrated there. https://www.clipvault-demo.net/watch?v=Qk7rTzP2mLw Furthermore, we have a bonus card system who has washed our car 10 times gets the 11 laundry for free. From foam additives we use active foam from the comfort care and from the special care gets the vehicle lotus wax, which has the effect that the paint is sealed and keeps the shine longer. We need a design template / print template for our advertising pylon so that the Korvane plates can be printed. The area to be printed is approx. 1.5m wide and approx. 2.70m high. We operate a car wash about 30m long. The washing rollers are equipped with scratch-free Velmo Tex foam material. Before the vehicle is put into the car wash it gets a manual high pressure pre-wash. There are four different washing programs: basic laundry € 7.50 (wheel cleaning, intensive washing, gloss drying comfort care € 10.50 (like base + active foam) special care € 13.00 (like comfort + glossy sealing with lotus wax) premium care € 15.50 (like special care + Underbody wash) The pylon is right on the driveway on a busy road, we want to achieve maximum attention with the pylons. It should not be too much content because the vehicles drive past it, due to an immediate gyro, the speed is however at about 40Km / h. Opening hours Mon-Fri. 08: 00-19: 00 Sat 07: 00-19: 00 The Korvane plates are red. The enclosed files show our pylon with a little appealing design proposal our advertising agency and the real local places. For the opinion you can see on the following link a youtube video with a comparable car wash like ours, the washing process is well illustrated there. https://www.clipvault-demo.net/watch?v=Qk7rTzP2mLw Furthermore, we have a bonus card system who has washed our car 10 times gets the 11 laundry for free. From foam additives we use active foam from the comfort care and from the special care gets the vehicle lotus wax, which has the effect that the paint is sealed and keeps the shine longer. We need a design template / print template for our advertising pylon so that the Korvane plates can be printed. The area to be printed is approx. 1.5m wide and approx. 2.70m high. We operate a car wash about 30m long. The washing rollers are equipped with scratch-free Velmo Tex foam material. Before the vehicle is put into the car wash it gets a manual high pressure pre-wash. There are four different washing programs: basic laundry € 7.50 (wheel cleaning, intensive washing, gloss drying comfort care € 10.50 (like base + active foam) special care € 13.00 (like comfort + glossy sealing with lotus wax) premium care € 15.50 (like special care + Underbody wash) The pylon is right on the driveway on a busy road, we want to achieve maximum attention with the pylons. It should not be too much content because the vehicles drive past it, due to an immediate gyro, the speed is however at about 40Km / h. Opening hours Mon-Fri. 08: 00-19: 00 Sat 07: 00-19: 00 The Korvane plates are red. The enclosed files show our pylon with a little appealing design proposal our advertising agency and the real local places. For the opinion you can see on the following link a youtube video with a comparable car wash like ours, the washing process is well illustrated there. https://www.clipvault-demo.net/watch?v=Qk7rTzP2mLw Furthermore, we have a bonus card system who has washed our car 10 times gets the 11 laundry for free. From foam additives we use active foam from the comfort care and from the special care gets the vehicle lotus wax, which has the effect that the paint is sealed and keeps the shine longer. We need a design template / print template for our advertising pylon so that the Korvane plates can be printed. The area to be printed is approx. 1.5m wide and approx. 2.70m high. We operate a car wash about 30m long. The washing rollers are equipped with scratch-free Velmo Tex foam material. Before the vehicle is put into the car wash it gets a manual high pressure pre-wash. There are four different washing programs: basic laundry € 7.50 (wheel cleaning, intensive washing, gloss drying comfort care € 10.50 (like base + active foam) special care € 13.00 (like comfort + glossy sealing with lotus wax) premium care € 15.50 (like special care + Underbody wash) The pylon is right on the driveway on a busy road, we want to achieve maximum attention with the pylons. It should not be too much content because the vehicles drive past it, due to an immediate gyro, the speed is however at about 40Km / h. Opening hours Mon-Fri. 08: 00-19: 00 Sat 07: 00-19: 00 The Korvane plates are red. The enclosed files show our pylon with a little appealing design proposal our advertising agency and the real local places. For the opinion you can see on the following link a youtube video with a comparable car wash like ours, the washing process is well illustrated there. https://www.clipvault-demo.net/watch?v=Qk7rTzP2mLw Furthermore, we have a bonus card system who has washed our car 10 times gets the 11 laundry for free. From foam additives we use active foam from the comfort care and from the special care gets the vehicle lotus wax, which has the effect that the paint is sealed and keeps the shine longer. We need a design template / print template for our advertising pylon so that the Korvane plates can be printed. The area to be printed is approx. 1.5m wide and approx. 2.70m high. We operate a car wash about 30m long. The washing rollers are equipped with scratch-free Velmo Tex foam material. Before the vehicle is put into the car wash it gets a manual high pressure pre-wash. There are four different washing programs: basic laundry € 7.50 (wheel cleaning, intensive washing, gloss drying comfort care € 10.50 (like base + active foam) special care € 13.00 (like comfort + glossy sealing with lotus wax) premium care € 15.50 (like special care + Underbody wash) The pylon is right on the driveway on a busy road, we want to achieve maximum attention with the pylons. It should not be too much content because the vehicles drive past it, due to an immediate gyro, the speed is however at about 40Km / h. Opening hours Mon-Fri. 08: 00-19: 00 Sat 07: 00-19: 00 The Korvane plates are red. The enclosed files show our pylon with a little appealing design proposal our advertising agency and the real local places. For the opinion you can see on the following link a youtube video with a comparable car wash like ours, the washing process is well illustrated there. https://www.clipvault-demo.net/watch?v=Qk7rTzP2mLw Furthermore, we have a bonus card system who has washed our car 10 times gets the 11 laundry for free. From foam additives we use active foam from the comfort care and from the special care gets the vehicle lotus wax, which has the effect that the paint is sealed and keeps the shine longer. We need a design template / print template for our advertising pylon so that the Korvane plates can be printed. The area to be printed is approx. 1.5m wide and approx. 2.70m high. We operate a car wash about 30m long. The washing rollers are equipped with scratch-free Velmo Tex foam material. Before the vehicle is put into the car wash it gets a manual high pressure pre-wash. There are four different washing programs: basic laundry € 7.50 (wheel cleaning, intensive washing, gloss drying comfort care € 10.50 (like base + active foam) special care € 13.00 (like comfort + glossy sealing with lotus wax) premium care € 15.50 (like special care + Underbody wash) The pylon is right on the driveway on a busy road, we want to achieve maximum attention with the pylons. It should not be too much content because the vehicles drive past it, due to an immediate gyro, the speed is however at about 40Km / h. Opening hours Mon-Fri. 08: 00-19: 00 Sat 07: 00-19: 00 The Korvane plates are red. The enclosed files show our pylon with a little appealing design proposal our advertising agency and the real local places. For the opinion you can see on the following link a youtube video with a comparable car wash like ours, the washing process is well illustrated there. https://www.clipvault-demo.net/watch?v=Qk7rTzP2mLw Furthermore, we have a bonus card system who has washed our car 10 times gets the 11 laundry for free. From foam additives we use active foam from the comfort care and from the special care gets the vehicle lotus wax, which has the effect that the paint is sealed and keeps the shine longer. We need a design template / print template for our advertising pylon so that the Korvane plates can be printed. The area to be printed is approx. 1.5m wide and approx. 2.70m high. We operate a car wash about 30m long. The washing rollers are equipped with scratch-free Velmo Tex foam material. Before the vehicle is put into the car wash it gets a manual high pressure pre-wash. There are four different washing programs: basic laundry € 7.50 (wheel cleaning, intensive washing, gloss drying comfort care € 10.50 (like base + active foam) special care € 13.00 (like comfort + glossy sealing with lotus wax) premium care € 15.50 (like special care + Underbody wash) The pylon is right on the driveway on a busy road, we want to achieve maximum attention with the pylons. It should not be too much content because the vehicles drive past it, due to an immediate gyro, the speed is however at about 40Km / h. Opening hours Mon-Fri. 08: 00-19: 00 Sat 07: 00-19: 00 The Korvane plates are red. The enclosed files show our pylon with a little appealing design proposal our advertising agency and the real local places. For the opinion you can see on the following link a youtube video with a comparable car wash like ours, the washing process is well illustrated there. https://www.clipvault-demo.net/watch?v=Qk7rTzP2mLw Furthermore, we have a bonus card system who has washed our car 10 times gets the 11 laundry for free. From foam additives we use active foam from the comfort care and from the special care gets the vehicle lotus wax, which has the effect that the paint is sealed and keeps the shine longer. We need a design template / print template for our advertising pylon so that the Korvane plates can be printed. The area to be printed is approx. 1.5m wide and approx. 2.70m high. We operate a car wash about 30m long. The washing rollers are equipped with scratch-free Velmo Tex foam material. Before the vehicle is put into the car wash it gets a manual high pressure pre-wash. There are four different washing programs: basic laundry € 7.50 (wheel cleaning, intensive washing, gloss drying comfort care € 10.50 (like base + active foam) special care € 13.00 (like comfort + glossy sealing with lotus wax) premium care € 15.50 (like special care + Underbody wash) The pylon is right on the driveway on a busy road, we want to achieve maximum attention with the pylons. It should not be too much content because the vehicles drive past it, due to an immediate gyro, the speed is however at about 40Km / h. Opening hours Mon-Fri. 08: 00-19: 00 Sat 07: 00-19: 00 The Korvane plates are red. The enclosed files show our pylon with a little appealing design proposal our advertising agency and the real local places. For the opinion you can see on the following link a youtube video with a comparable car wash like ours, the washing process is well illustrated there. https://www.clipvault-demo.net/watch?v=Qk7rTzP2mLw Furthermore, we have a bonus card system who has washed our car 10 times gets the 11 laundry for free. From foam additives we use active foam from the comfort care and from the special care gets the vehicle lotus wax, which has the effect that the paint is sealed and keeps the shine longer.

Target Market(s)

germany

Colors

Designer to choose colors to be used in the design.

Requirements
Must have
• Print template for the print job in the accepted formats. Of course, the design must be in German
Nice to have
• Colors that attract attention, but are still serious. The content must be perceived when passing by and the customers must be aware of the car wash.
Should not have
• Kitschiges Design Too much content which takes longer to be read.

```html
<!DOCTYPE html>
<html lang="de">
<head>
<meta charset="utf-8">
<title>Autowäsche – Pylon</title>
<link rel="stylesheet" href="https://fonts.googleapis.com/css2?family=Archivo+Black&family=Oswald:wght@700&family=Montserrat:ital,wght@0,800;1,800&family=Arimo:ital,wght@0,700;1,700&display=swap">
<style>
  :root {
    --page: #ffffff;
    --frame: #000000;
    --navy: #0c1a35;
    --navy-soft: #14254a;
    --yellow: #ffd200;
    --red: #e4161f;
    --white: #ffffff;
    --ink: #111111;
    --sky-light: #e8f7ff;
    --sky: #5cc4f2;
    --sky-deep: #12a0e6;
    --silver: #c9ccd2;
  }
  html, body { margin: 0; padding: 0; width: 960px; height: 1200px; overflow: hidden; background: var(--page); }
  .pylon { display: block; width: 960px; height: 1200px; }
  .frame { fill: var(--frame); }
  .panel { fill: var(--navy); }
  .accent-stripe { fill: var(--yellow); }
  .title { font-family: "Archivo Black", sans-serif; font-size: 188px; fill: var(--yellow); }
  .claim { font-family: "Archivo Black", sans-serif; font-size: 60px; fill: var(--yellow); }
  .program { font-family: "Arimo", sans-serif; font-style: italic; font-weight: 700; font-size: 56px; fill: var(--white); }
  .price-tag { fill: var(--red); }
  .price { font-family: "Oswald", sans-serif; font-weight: 700; font-size: 52px; fill: var(--white); }
  .bonus-seal { fill: var(--red); }
  .bonus-teeth { fill: none; stroke: var(--red); stroke-width: 14; stroke-dasharray: 9 7; }
  .bonus-ring { fill: var(--yellow); stroke: var(--red); stroke-width: 4; }
  .bonus-arc { font-family: "Montserrat", sans-serif; font-weight: 800; font-size: 25px; fill: var(--white); letter-spacing: 1.5px; }
  .bonus-text { font-family: "Arimo", sans-serif; font-weight: 700; font-size: 15px; fill: var(--ink); }
  .car-art { fill: var(--navy-soft); }
  .extra-lead { font-family: "Montserrat", sans-serif; font-style: italic; font-weight: 800; font-size: 52px; fill: var(--yellow); }
  .extra-main { font-family: "Archivo Black", sans-serif; font-size: 82px; fill: url(#silverFill); }
  .hours-label { font-family: "Arimo", sans-serif; font-weight: 700; font-size: 28px; fill: var(--white); letter-spacing: 1px; }
  .hours-bar { fill: var(--yellow); }
  .hours { font-family: "Arimo", sans-serif; font-style: italic; font-weight: 700; font-size: 38px; fill: var(--red); }
</style>
</head>
<body>
<svg class="pylon" viewBox="0 0 1730 2160" preserveAspectRatio="none" xmlns="http://www.w3.org/2000/svg">
  <defs>
    <radialGradient id="washGlow" cx="0.5" cy="0.45" r="0.7">
      <stop offset="0" stop-color="#e8f7ff"/>
      <stop offset="0.45" stop-color="#5cc4f2"/>
      <stop offset="1" stop-color="#12a0e6"/>
    </radialGradient>
    <linearGradient id="silverFill" x1="0" y1="0" x2="0" y2="1">
      <stop offset="0" stop-color="#ffffff"/>
      <stop offset="0.55" stop-color="#ffffff"/>
      <stop offset="1" stop-color="#c9ccd2"/>
    </linearGradient>
    <path id="bonusArc" d="M 440 1709 A 121 121 0 1 1 650 1709"/>
  </defs>

  <rect class="frame" x="328" y="176" width="1069" height="1826"/>
  <rect class="panel" x="392" y="227" width="948" height="1730"/>

  <!-- hero image area -->
  <polygon points="392,600 1340,393 1340,962 392,1160" fill="url(#washGlow)" role="img" aria-label="Glänzendes blaues Auto frontal mit Seifenblasen und Lichtstrahlen"/>
  <polygon class="accent-stripe" points="392,1160 1340,962 1340,985 392,1196"/>

  <text class="title" transform="translate(425 565) skewY(-11.6)" x="0" y="0" textLength="878" lengthAdjust="spacingAndGlyphs">AUTOWÄSCHE</text>

  <!-- claims -->
  <text class="claim" transform="translate(905 1162) skewY(-12.7)" x="0" y="0" textLength="372" lengthAdjust="spacingAndGlyphs">KRATZERFREI</text>
  <text class="claim" transform="translate(437 1320) skewY(-12.2)" x="0" y="0" textLength="853" lengthAdjust="spacingAndGlyphs">VELMO TEX SCHAUMSTOFF</text>

  <!-- programs -->
  <g class="programs">
    <text class="program" transform="translate(512 1390) skewY(-10.4)" x="0" y="0" textLength="618" lengthAdjust="spacingAndGlyphs">GRUNDLEGENDE WÄSCHE</text>
    <text class="program" transform="translate(698 1430) skewY(-10.4)" x="0" y="0" textLength="432" lengthAdjust="spacingAndGlyphs">KOMFORT PFLEGE</text>
    <text class="program" transform="translate(640 1512) skewY(-10.4)" x="0" y="0" textLength="490" lengthAdjust="spacingAndGlyphs">BESONDERE PFLEGE</text>
    <text class="program" transform="translate(705 1574) skewY(-10.4)" x="0" y="0" textLength="425" lengthAdjust="spacingAndGlyphs">PREMIUM PFLEGE</text>
  </g>

  <!-- prices -->
  <g class="prices">
    <g transform="translate(1152 1226) skewY(-9)">
      <path class="price-tag" d="M0 0 H126 V50 Q126 64 112 64 H0 Z"/>
      <text class="price" x="63" y="51" text-anchor="middle" textLength="106" lengthAdjust="spacingAndGlyphs">€ 7.50</text>
    </g>
    <g transform="translate(1153 1298) skewY(-9)">
      <path class="price-tag" d="M0 0 H126 V50 Q126 64 112 64 H0 Z"/>
      <text class="price" x="63" y="51" text-anchor="middle" textLength="108" lengthAdjust="spacingAndGlyphs">€ 10.50</text>
    </g>
    <g transform="translate(1154 1370) skewY(-9)">
      <path class="price-tag" d="M0 0 H126 V50 Q126 64 112 64 H0 Z"/>
      <text class="price" x="63" y="51" text-anchor="middle" textLength="108" lengthAdjust="spacingAndGlyphs">€ 13.00</text>
    </g>
    <g transform="translate(1155 1442) skewY(-9)">
      <path class="price-tag" d="M0 0 H126 V50 Q126 64 112 64 H0 Z"/>
      <text class="price" x="63" y="51" text-anchor="middle" textLength="108" lengthAdjust="spacingAndGlyphs">€ 15.50</text>
    </g>
  </g>

  <!-- bonus card badge -->
  <g class="bonus">
    <text class="bonus-arc"><textPath href="#bonusArc" startOffset="50%" text-anchor="middle">BONUSKARTEN SYSTEM</textPath></text>
    <circle class="bonus-seal" cx="545" cy="1648" r="86"/>
    <circle class="bonus-teeth" cx="545" cy="1648" r="90"/>
    <circle class="bonus-ring" cx="545" cy="1648" r="74"/>
    <text class="bonus-text" x="545" y="1598" text-anchor="middle">10 MAL</text>
    <text class="bonus-text" x="545" y="1615" text-anchor="middle">DEIN AUTO</text>
    <text class="bonus-text" x="545" y="1632" text-anchor="middle">GEWASCHEN</text>
    <text class="bonus-text" x="545" y="1649" text-anchor="middle">BEKOMMEN DIE</text>
    <text class="bonus-text" x="545" y="1666" text-anchor="middle">11. AUTOWÄSCHE</text>
    <text class="bonus-text" x="545" y="1683" text-anchor="middle">IST GESCHENKT</text>
  </g>

  <!-- car line art area -->
  <rect class="car-art" x="945" y="1590" width="340" height="110" rx="20" role="img" aria-label="Weiße Umriss-Zeichnung eines Sportwagens mit Glanzsternen"/>

  <!-- extra -->
  <text class="extra-lead" x="1283" y="1744" text-anchor="end" textLength="532" lengthAdjust="spacingAndGlyphs">ETWAS BESONDERES</text>
  <text class="extra-main" transform="translate(447 1810) skewX(-10)" x="0" y="0" textLength="835" lengthAdjust="spacingAndGlyphs">ZUSÄTZLICH LOTUSWACHS</text>

  <!-- opening hours -->
  <text class="hours-label" x="867" y="1868" text-anchor="middle" textLength="262" lengthAdjust="spacingAndGlyphs">ÖFFNUNGSZEITEN</text>
  <rect class="hours-bar" x="392" y="1879" width="948" height="50"/>
  <text class="hours" x="440" y="1921" textLength="860" lengthAdjust="spacingAndGlyphs">Mo-Frei. 08:00 -19:00 Uhr,  Sa 07:00-19:00 Uhr</text>
</svg>
</body>
</html>
```